real esate business card with company logo and name

we need a business card design for a real esate company

The company name is Walsh & Brand Pty Ltd, and we have our logo designed and will upload. We want classic or moden feel. Black or white background. looks more textured. Should include folowinginformations
Owen Walsh and Lucy Brand
Sales Agents & Onsite Manager
p: 07 5948 2063
F: 07 5948 2174
M:0431 857 219
3/42 Marlow Crescent, FERNLEA QLD 4213

We want this business card looks professonal. Thank you in advance.

Industry/Entity Type

Real Estate Agent

Contact Information for Business Card

Owen Walsh and Lucy Brand
Onsite Manager & Sales Agents
p: 07 5948 2063
M:0431 857 219

Font styles to use
Serif

Colors
000000
fbfbfb
333333
959595

Requirements
Must have
• company logo and name, black or white back ground

```html
<!DOCTYPE html>
<html lang="en">
<head>
<meta charset="utf-8">
<title>Walsh &amp; Brand Pty Ltd — Business Card</title>
<link rel="stylesheet" href="https://fonts.googleapis.com/css2?family=Alegreya+Sans:wght@700;800&family=Open+Sans:wght@700&display=swap">
<style>
  :root {
    --ink-black: #000000;
    --paper-white: #fbfbfb;
    --charcoal: #333333;
    --stone: #959595;
    --label-grey: #6a6a6a;
    --tagline-grey: #5c5c5c;
  }
  * { margin: 0; padding: 0; box-sizing: border-box; }
  html, body {
    width: 1200px;
    height: 686px;
    overflow: hidden;
    background: var(--ink-black);
  }
  .card {
    position: relative;
    width: 1200px;
    height: 686px;
    overflow: hidden;
    font-variant-numeric: lining-nums;
    background:
      radial-gradient(ellipse 70% 90% at 85% 30%, rgba(80,80,80,0.55), rgba(0,0,0,0) 70%),
      linear-gradient(100deg, var(--ink-black) 0%, #0b0b0b 35%, #262626 70%, var(--charcoal) 100%);
  }
  .brand {
    position: absolute;
    left: 64px;
    top: 110px;
    width: 460px;
    display: flex;
    flex-direction: column;
    align-items: center;
  }
  .brand__mark {
    width: 250px;
    height: 250px;
    background: var(--stone);
  }
  .brand__name {
    margin-top: 78px;
    font-family: "Alegreya Sans", sans-serif;
    font-weight: 700;
    font-size: 36px;
    line-height: 1;
    letter-spacing: 2px;
    text-transform: uppercase;
    color: var(--stone);
    white-space: nowrap;
  }
  .agents {
    position: absolute;
    left: 560px;
    top: 88px;
    width: 590px;
    text-align: center;
  }
  .agents__names {
    font-family: "Alegreya Sans", sans-serif;
    font-weight: 800;
    font-size: 46px;
    line-height: 1;
    color: var(--paper-white);
    white-space: nowrap;
  }
  .agents__role {
    margin-top: 6px;
    font-family: "Open Sans", sans-serif;
    font-weight: 700;
    font-size: 25px;
    line-height: 1;
    color: var(--tagline-grey);
    white-space: nowrap;
  }
  .contact {
    position: absolute;
    right: 64px;
    top: 414px;
    list-style: none;
    text-align: right;
    font-family: "Alegreya Sans", sans-serif;
    font-weight: 800;
    font-size: 40px;
    line-height: 51px;
    color: var(--paper-white);
    white-space: nowrap;
  }
  .contact__label {
    color: var(--label-grey);
    margin-right: 14px;
  }
  .contact__label--tight { margin-right: 6px; }
</style>
</head>
<body>
  <main class="card">
    <section class="brand">
      <div class="brand__mark" role="img" aria-label="Walsh &amp; Brand logo mark"></div>
      <p class="brand__name">Walsh &amp; Brand Pty Ltd</p>
    </section>

    <header class="agents">
      <h1 class="agents__names">Owen Walsh and Lucy Brand</h1>
      <p class="agents__role">Onsite Manager &amp; Sales Agents</p>
    </header>

    <ul class="contact">
      <li><span class="contact__label">P</span>07 5948 2063</li>
      <li><span class="contact__label">M</span>0431 857 219</li>
      <li><span class="contact__label contact__label--tight">A</span>3/42 Marlow Crescent</li>
      <li>FERNLEA QLD 4213</li>
    </ul>
  </main>
</body>
</html>
```